Professional "Save the Date" Design

We are looking for a professional designer to create a clean, modern, and eye-catching "Save the Date" invitation that will be sent to a select group of physicians participating in our BRIGHTLANE Study.
Key Requirements:
The KORMAL logo should be clearly featured and lead the branding.
The OMBRA FLEX TQ logo should also appear but be subordinate to the KORMAL logo.
The design should be professional, modern, and easy to read — no busy or cluttered layouts.
The final product will be used in email communications (PDF or image format).
The project is time-sensitive: we would like to have the final version completed by end of day tomorrow.
Deliverables:
Final design in high-resolution PDF and image formats (PNG or JPG).
Editable file (Adobe Illustrator, InDesign, or similar) if possible.
Details:
Monday, June 23, 2025
4:30-5:15pm EST
Name of Call: BRIGHTLANE Investigator Call
Location: Virtual (PELTA Call)
Please include this blurb as well: "Join us for a BRIGHTLANE Study Investigator Call as we welcome all participating sites and provide key information to support a successful launch. We’ll cover points of contact, upcoming study-related events, and next steps as we begin site activation."
Physicians
Medical Device

```html
<!DOCTYPE html>
<html lang="en">
<head>
<meta charset="utf-8">
<title>Save the Date – BRIGHTLANE Investigator Call</title>
<link rel="stylesheet" href="https://fonts.googleapis.com/css2?family=Crimson+Pro:wght@700&family=Montserrat:wght@300;700&family=Barlow:wght@400;500;600&display=swap">
<style>
  :root {
    --green-dark: #2f5b24;
    --green-light: #6cb33f;
    --purple: #a3238e;
    --navy: #1c2147;
    --paper: #fbfdf9;
    --pattern-tint: #eef5ea;
  }
  * { margin: 0; padding: 0; box-sizing: border-box; }
  html, body { width: 858px; height: 1200px; overflow: hidden; }
  body { background: var(--paper); }
  .invite {
    position: relative;
    width: 858px;
    height: 1200px;
    overflow: hidden;
    background: radial-gradient(circle at 50% 40%, var(--paper) 0%, var(--pattern-tint) 100%);
    color: var(--green-dark);
  }
  .headline {
    position: absolute;
    left: 204px;
    top: 108px;
    font-family: "Crimson Pro", Georgia, serif;
    font-weight: 700;
    color: var(--green-dark);
    line-height: 1;
  }
  .headline .initial {
    position: absolute;
    left: 0;
    top: 0;
    font-size: 170px;
    line-height: 1;
  }
  .headline .word {
    position: absolute;
    font-size: 96px;
    line-height: 1;
    white-space: nowrap;
  }
  .headline .ave { left: 88px; top: 6px; }
  .headline .the { left: 98px; top: 84px; }
  .headline .date { left: 6px; top: 132px; font-size: 112px; }
  .headline .date span { font-size: 150px; }
  .divider-vertical {
    position: absolute;
    left: 465px;
    top: 128px;
    width: 2px;
    height: 272px;
    background: var(--purple);
  }
  .tag-invitation {
    position: absolute;
    left: 473px;
    top: 350px;
    transform-origin: 0 0;
    transform: rotate(-90deg);
    font-family: "Montserrat", Arial, sans-serif;
    font-weight: 300;
    font-size: 35px;
    letter-spacing: 1px;
    color: var(--purple);
    white-space: nowrap;
  }
  .stethoscope-art {
    position: absolute;
    left: 520px;
    top: 108px;
    width: 126px;
    height: 300px;
    border-radius: 60px 60px 40px 40px;
    background: linear-gradient(180deg, #a8d48b 0%, var(--green-light) 100%);
    opacity: 0.55;
  }
  .rule {
    position: absolute;
    left: 238px;
    width: 388px;
    height: 2px;
    background: linear-gradient(90deg, rgba(163,35,142,0) 0%, var(--purple) 50%, rgba(163,35,142,0) 100%);
  }
  .rule-1 { top: 487px; }
  .rule-2 { top: 690px; }
  .rule-3 { top: 806px; }
  .when {
    position: absolute;
    left: 0;
    width: 858px;
    text-align: center;
    font-family: "Montserrat", Arial, sans-serif;
    color: var(--green-dark);
  }
  .when-day { top: 499px; font-weight: 700; font-size: 44px; letter-spacing: 1px; }
  .when-date { top: 538px; font-size: 74px; letter-spacing: -1px; }
  .when-date .month { font-weight: 300; }
  .when-date .num { font-weight: 700; }
  .when-time { top: 620px; font-size: 41px; font-weight: 700; }
  .when-time .zone { font-weight: 300; }
  .details {
    position: absolute;
    left: 0;
    top: 720px;
    width: 858px;
    text-align: center;
    font-family: "Barlow", Arial, sans-serif;
    font-size: 22px;
    line-height: 28px;
    letter-spacing: 0.3px;
  }
  .details .label { color: var(--green-light); }
  .details .value { color: var(--green-dark); font-weight: 500; }
  .blurb {
    position: absolute;
    left: 169px;
    top: 834px;
    width: 520px;
    font-family: "Barlow", Arial, sans-serif;
    font-size: 16.5px;
    line-height: 21px;
    letter-spacing: 0.4px;
    color: var(--green-light);
    text-align: justify;
    text-align-last: center;
    text-transform: uppercase;
  }
  .brand-row {
    position: absolute;
    left: 240px;
    top: 995px;
    width: 388px;
    height: 92px;
    display: flex;
    align-items: center;
    justify-content: space-between;
  }
  .brand {
    font-family: "Barlow", Arial, sans-serif;
    font-weight: 600;
    white-space: nowrap;
    line-height: 1;
  }
  .brand-lead {
    font-size: 54px;
    color: var(--green-light);
  }
  .brand-partner {
    font-size: 19px;
    letter-spacing: 0.3px;
    color: var(--purple);
  }
</style>
</head>
<body>
  <main class="invite">
    <h1 class="headline" aria-label="Save the Date">
      <span class="initial">S</span>
      <span class="word ave">ave</span>
      <span class="word the">the</span>
      <span class="word date"><span>D</span>ate</span>
    </h1>
    <div class="divider-vertical"></div>
    <div class="tag-invitation">INVITATION</div>
    <div class="stethoscope-art" role="img" aria-label="Green stethoscope illustration wrapping around the headline"></div>

    <div class="rule rule-1"></div>
    <p class="when when-day">MONDAY,</p>
    <p class="when when-date"><span class="month">JUNE</span> <span class="num">23, 2025</span></p>
    <p class="when when-time">4:30-5:15PM <span class="zone">EST</span></p>
    <div class="rule rule-2"></div>

    <div class="details">
      <p><span class="label">NAME OF CALL:</span> <span class="value">BRIGHTLANE INVESTIGATOR CALL</span></p>
      <p><span class="label">LOCATION:</span> <span class="value">VIRTUAL (PELTA CALL)</span></p>
    </div>
    <div class="rule rule-3"></div>

    <p class="blurb">Join us for a BRIGHTLANE Study Investigator Call as we welcome all participating sites and provide key information to support a successful launch. We’ll cover points of contact, upcoming study-related events, and next steps as we begin site activation</p>

    <div class="brand-row">
      <div class="brand brand-lead">KORMAL</div>
      <div class="brand brand-partner">OMBRA FLEX TQ</div>
    </div>
  </main>
</body>
</html>
```